Hunting Ethics Organization Needs a Web Design with Logo Refresh

This project involves the creation of a website design including the homepage design, inside page design, and logo refinements. Our organization is Tessaly, and we are a not-for-profit hunting ethics organization.
The focus of the new website design is to bring attention the mission of our organization, provide an overview of the areas where our organization deploys its resources to support the modern hunter, and to encourage visitors to support our organization by donating in support of the organization’s mission.
The winning design will be implemented in Wordpress by our in-house team. If you have questions about how any particular design element may translate to Wordpress, please feel free to post questions in response to this brief. In general, however, we’re more focused on the evolution and delivery of a strong overall design aesthetic – we’ll shoulder the responsibility of how we translate that design into Wordpress.
See attached design brief for full details.

```html
<!DOCTYPE html>
<html lang="en">
<head>
<meta charset="utf-8">
<title>Tessaly – Protect the heritage of hunting</title>
<link href="https://fonts.googleapis.com/css2?family=Open+Sans:wght@400;600;700;800&display=swap" rel="stylesheet">
<style>
:root{
  --cream:#efeedf;
  --white:#ffffff;
  --olive:#a59f68;
  --olive-dark:#8c8652;
  --blue:#1d5a8e;
  --blue-dark:#174b78;
  --ink:#3b3b3b;
  --muted:#6d6d6d;
  --bar:#3a3a3a;
}
*{box-sizing:border-box;margin:0;padding:0}
html,body{width:1200px;height:4111px;overflow:hidden}
body{font-family:"Open Sans",Arial,sans-serif;color:var(--ink);background:var(--white);position:relative}
section,header,footer{position:relative;width:1200px}
.abs{position:absolute}
a{color:inherit;text-decoration:none}

/* header */
.site-header{height:103px;background:var(--white)}
.brand{left:130px;top:20px;display:flex;flex-direction:column}
.brand-name{font-size:40px;font-weight:800;color:var(--blue);letter-spacing:1px;line-height:1;display:flex;align-items:center;gap:8px}
.brand-name .dot{width:14px;height:14px;border-radius:50%;background:var(--olive)}
.brand-tag{font-size:11px;font-weight:600;color:var(--blue);letter-spacing:1px;margin-top:4px}
.main-nav{right:120px;top:48px;display:flex;gap:22px;align-items:center;font-size:13px;color:var(--blue-dark);text-transform:uppercase}
.btn-donate{background:var(--olive);color:var(--white);font-weight:700;padding:8px 22px;font-size:12px}

/* hero */
.hero{height:555px;background:linear-gradient(180deg,#8a95a6 0%,#a7a9a3 40%,#9f8a64 70%,#5d4b33 100%)}
.hero-copy{left:147px;top:205px;color:var(--white);width:420px}
.hero h1{font-size:64px;font-weight:800;letter-spacing:2px;line-height:1}
.hero h2{font-size:34px;font-weight:700;margin-top:14px}
.hero p{font-size:13px;line-height:19px;margin-top:20px}
.btn-learn{display:inline-block;background:var(--olive);color:var(--white);font-size:13px;font-weight:700;padding:8px 20px;margin-top:40px}

/* shared */
.section-title{font-size:22px;font-weight:700;text-align:center;letter-spacing:1px;color:var(--ink);text-transform:uppercase}
.section-lead{font-size:13px;line-height:22px;text-align:center;color:var(--muted);width:940px;margin:14px auto 0}

/* help */
.help{height:432px;background:var(--cream);padding-top:90px}
.cause{top:227px;height:103px;width:295px;display:flex}
.cause-num{width:72px;height:103px;background:var(--olive);color:var(--white);font-size:46px;font-weight:700;display:flex;align-items:center;justify-content:center;border:4px solid var(--cream);outline:2px solid var(--olive)}
.cause-body{flex:1;height:80px;margin-top:11px;background:var(--blue);clip-path:polygon(0 0,100% 0,88% 100%,0 100%);color:var(--white);padding:18px 16px}
.cause-body h3{font-size:18px;font-weight:700;text-transform:uppercase}
.cause-body span{font-size:11px}

/* gallery */
.works{height:686px;background:var(--white);padding-top:90px}
.tile{width:305px;height:220px}

/* support */
.support{height:665px;background:var(--cream);padding-top:88px}
.pillar{width:300px}
.pillar-head{display:flex;align-items:center;gap:14px}
.pillar-num{width:40px;height:40px;background:var(--muted);color:var(--white);font-weight:700;font-size:24px;display:flex;align-items:center;justify-content:center}
.pillar-head h3{font-size:17px;font-weight:700;color:var(--olive);text-transform:uppercase}
.pillar-rule{width:70px;height:2px;background:var(--olive);margin:8px 0 0 54px}
.pillar p{font-size:12px;line-height:18px;color:var(--muted);margin-top:14px}
.read-more{font-size:13px;color:var(--ink);display:block;margin-top:8px;text-transform:uppercase}

/* news */
.news{height:535px;background:var(--white);padding-top:92px}
.post{width:290px;top:245px}
.post h3{font-size:18px;font-weight:700;color:var(--olive);text-transform:uppercase}
.post-rule{width:290px;height:1px;background:#d7d7d7;margin-top:8px}
.post p{font-size:12px;line-height:19px;color:var(--muted);margin-top:16px}
.post .read-more{margin-top:28px}

/* testimonials */
.testimonials{height:555px;background:var(--cream);padding-top:95px}
.testimonials::before{content:"";position:absolute;left:560px;top:0;border-left:40px solid transparent;border-right:40px solid transparent;border-top:30px solid var(--white)}
.quote-by{text-align:center;font-size:14px;margin-top:28px}
.quote-by .name{color:var(--olive)}
.avatar{top:3287px;width:136px;height:136px;border-radius:50%;border:5px solid var(--white);background:radial-gradient(circle at 50% 40%,#c7c2b8,#7d7a74)}
.dots{left:578px;top:3470px;display:flex;gap:10px}
.dots span{width:11px;height:11px;border-radius:50%;background:#b9b8ae}

/* partners */
.partners{height:230px;background:var(--white)}
.partner-row{left:215px;top:100px;width:770px;display:flex;justify-content:space-between;align-items:center}
.partner{display:flex;align-items:center;gap:8px;font-size:24px;font-weight:700;color:#555}
.partner i{width:14px;height:14px;background:#555;display:block}
.arrow{top:108px;width:22px;height:22px;border-radius:50%;background:var(--olive)}

/* footer */
.site-footer{height:268px;background:var(--blue);color:var(--white)}
.fcol{top:57px}
.fcol h4{font-size:13px;font-weight:700;text-transform:uppercase;padding-bottom:8px;border-bottom:1px solid #7ea0bf;width:120px}
.fcol ul{list-style:none;margin-top:10px}
.fcol li{font-size:12px;line-height:18px;color:#d6e2ee}
.news-form{top:170px;left:782px;display:flex}
.news-form .field{width:200px;height:34px;background:var(--white);color:#999;font-size:11px;padding:10px}
.news-form .go{width:88px;height:34px;background:var(--olive);font-size:12px;font-weight:700;display:flex;align-items:center;justify-content:center}
.bottom-bar{height:82px;background:var(--bar);color:#cfcfcf;font-size:11px}
.social{right:140px;top:30px;display:flex;gap:8px}
.social span{width:22px;height:22px;display:block}
</style>
</head>
<body>

<header class="site-header">
  <div class="abs brand">
    <div class="brand-name"><span class="dot"></span>TESSALY</div>
    <div class="brand-tag">FIELD ETHICS SOCIETY</div>
  </div>
  <nav class="abs main-nav">
    <a>About us</a><a>Hunting ethics</a><a>Conservation</a><a>Get involved</a><a>Contact us</a>
    <a class="btn-donate">DONATE</a>
  </nav>
</header>

<section class="hero" role="img" aria-label="Photograph of a hunter and a child walking through dry grassland toward mountains">
  <div class="abs hero-copy">
    <h1>TESSALY</h1>
    <h2>Protect the heritage Of hunting</h2>
    <p>We stand for fair chase, respect for wildlife and care for the land. Join a community of hunters who carry these values into every season and pass them to the next generation in the field.</p>
    <a class="btn-learn">LEARN MORE</a>
  </div>
</section>

<section class="help">
  <h2 class="section-title">Help us protect the future of hunting</h2>
  <p class="section-lead">Our work brings hunters, landowners and wildlife groups together around a shared code of conduct. Every gift helps us teach ethics, restore habitat and welcome new hunters into a proud outdoor tradition.</p>
  <div class="abs cause" style="left:130px"><div class="cause-num">1</div><div class="cause-body"><h3>Hunting ethic</h3><span>read more</span></div></div>
  <div class="abs cause" style="left:446px"><div class="cause-num">2</div><div class="cause-body"><h3>Conservation</h3><span>read more</span></div></div>
  <div class="abs cause" style="left:775px"><div class="cause-num">3</div><div class="cause-body"><h3>Get involved</h3><span>read more</span></div></div>
</section>

<section class="works">
  <h2 class="section-title">What we have done</h2>
  <div class="abs tile" style="left:127px;top:152px;background:linear-gradient(160deg,#8f8a6a,#5f5a3e)" role="img" aria-label="Photograph of a stag in a grassy clearing"></div>
  <div class="abs tile" style="left:446px;top:152px;background:linear-gradient(160deg,#a09a86,#6a604a)" role="img" aria-label="Photograph of a hunter in camouflage with a retriever dog"></div>
  <div class="abs tile" style="left:768px;top:152px;background:linear-gradient(160deg,#b8b0a0,#6b5c48)" role="img" aria-label="Photograph of hunters walking through a birch forest"></div>
  <div class="abs tile" style="left:127px;top:388px;background:linear-gradient(160deg,#a8a7a2,#5e5f58)" role="img" aria-label="Photograph of hunters walking in a snowy field"></div>
  <div class="abs tile" style="left:446px;top:388px;background:linear-gradient(160deg,#8c8270,#4e4636)" role="img" aria-label="Photograph of a hunter aiming a shotgun from cover"></div>
  <div class="abs tile" style="left:768px;top:388px;background:linear-gradient(160deg,#9a9a80,#5a5b44)" role="img" aria-label="Photograph of a hunter with a dog wading through a marsh"></div>
</section>

<section class="support">
  <h2 class="section-title">Support us as we empower the modern hunter</h2>
  <p class="section-lead">This is where your support goes. We fund training, field guides and land projects that help hunters act with care and skill. Each program below is built to keep hunting safe, fair and respected for years ahead.</p>
  <div class="abs pillar" style="left:137px;top:248px"><div class="pillar-head"><div class="pillar-num">1</div><h3>Voluptatem fugit</h3></div><div class="pillar-rule"></div><p>Field courses that teach safe handling, clean shots and respect for game, led by seasoned mentors in every region we serve across the year.</p><a class="read-more">Read more</a></div>
  <div class="abs pillar" style="left:456px;top:248px"><div class="pillar-head"><div class="pillar-num">2</div><h3>Aut illo omnis ipsa</h3></div><div class="pillar-rule"></div><p>Habitat work that restores wetlands, hedges and woodland so that wildlife can thrive and hunters have healthy land to walk on.</p><a class="read-more">Read more</a></div>
  <div class="abs pillar" style="left:782px;top:248px"><div class="pillar-head"><div class="pillar-num">3</div><h3>Nemo rem ipsam quasi</h3></div><div class="pillar-rule"></div><p>Youth programs that pair young people with trusted guides, building skill, patience and a lasting bond with the outdoors and its wildlife.</p><a class="read-more">Read more</a></div>
  <div class="abs pillar" style="left:137px;top:454px"><div class="pillar-head"><div class="pillar-num">4</div><h3>Dolores voluptatem</h3></div><div class="pillar-rule"></div><p>Research grants that track game numbers and inform fair seasons, sharing findings openly with hunters, farmers and local wildlife boards.</p><a class="read-more">Read more</a></div>
  <div class="abs pillar" style="left:456px;top:454px"><div class="pillar-head"><div class="pillar-num">5</div><h3>Perspiciatis beatae odi</h3></div><div class="pillar-rule"></div><p>Public outreach that explains the role of ethical hunting in conservation and answers questions honestly from people outside our sport.</p><a class="read-more">Read more</a></div>
  <div class="abs pillar" style="left:782px;top:454px"><div class="pillar-head"><div class="pillar-num">6</div><h3>Veritatis beatae eos</h3></div><div class="pillar-rule"></div><p>Member events that gather hunters for talks, range days and shared meals, keeping our community close and our standards high.</p><a class="read-more">Read more</a></div>
</section>

<section class="news">
  <h2 class="section-title">Our news</h2>
  <p class="section-lead">Stories from the field, updates on our projects and notes from members. Catch up on what we have been doing this season and where your help made a real difference.</p>
  <article class="abs post" style="left:127px"><h3>Voluptatem fugit</h3><div class="post-rule"></div><p>Our spring mentor weekend welcomed forty new hunters to the range. Volunteers taught safe carry, shot placement and field care, and every guest left with a signed ethics pledge and a plan for their first autumn hunt.</p><a class="read-more">Read more</a></article>
  <article class="abs post" style="left:456px"><h3>Sed enim accusantium</h3><div class="post-rule"></div><p>Work on the river marsh project is nearly done. Members planted reeds, cleared old fencing and built nesting boxes, giving ducks and waders safe cover ahead of the coming season and a healthy home for years.</p><a class="read-more">Read more</a></article>
  <article class="abs post" style="left:785px"><h3>Aut illo aut veritatis</h3><div class="post-rule"></div><p>We have released a new field guide on fair chase in plain language. It covers tracking, shot choice and recovery, and it is free to every member who wants a printed copy to keep close in the truck or pack.</p><a class="read-more">Read more</a></article>
</section>

<section class="testimonials">
  <h2 class="section-title">What they say</h2>
  <p class="section-lead">Tessaly gave me the confidence to hunt with care. The mentors were patient, the lessons were clear and I now teach my own children the same values. I am proud to support this work every year.</p>
  <p class="quote-by"><span class="name">MARCUS HALE</span> - Ridgeway</p>
</section>
<div class="abs avatar" style="left:296px" role="img" aria-label="Portrait photo of a member"></div>
<div class="abs avatar" style="left:536px" role="img" aria-label="Portrait photo of a member"></div>
<div class="abs avatar" style="left:776px" role="img" aria-label="Portrait photo of a member"></div>
<div class="abs dots"><span></span><span></span><span></span></div>

<section class="partners">
  <span class="abs arrow" style="left:133px"><svg width="22" height="22" viewBox="0 0 22 22"><path d="M13 6l-5 5 5 5" fill="none" stroke="#fff" stroke-width="2"/></svg></span>
  <div class="abs partner-row">
    <span class="partner">Halvern<i></i></span>
    <span class="partner">Axora</span>
    <span class="partner">Cadmere</span>
    <span class="partner">Cityvale</span>
    <span class="partner"><i></i>Crestline</span>
  </div>
  <span class="abs arrow" style="left:1042px"><svg width="22" height="22" viewBox="0 0 22 22"><path d="M9 6l5 5-5 5" fill="none" stroke="#fff" stroke-width="2"/></svg></span>
</section>

<footer class="site-footer">
  <div class="abs fcol" style="left:127px"><h4>Company</h4><ul><li>Who we are</li><li>What we do</li><li>Company profile</li><li>What they say</li><li>Our executive team</li></ul></div>
  <div class="abs fcol" style="left:305px"><h4>Address</h4><ul><li>12 Marsh Lane</li><li>Unit 4</li><li>Fernhill</li><li>North Vale</li><li>Westmoor</li><li>Country</li></ul></div>
  <div class="abs fcol" style="left:463px"><h4>Support</h4><ul><li>Forum</li><li>FAQ</li><li>Contact</li><li>Chat</li><li>Find site</li></ul></div>
  <div class="abs fcol" style="left:617px"><h4>Other links</h4><ul><li>Social one</li><li>Social two</li><li>Social three</li><li>Social four</li><li>RSS</li></ul></div>
  <div class="abs fcol" style="left:782px"><h4 style="width:288px">Newsletter</h4><ul><li>Sign up for news from the field and our</li><li>latest projects, sent once a month.</li></ul></div>
  <div class="abs news-form"><span class="field">enter your email</span><span class="go">SEND</span></div>
</footer>

<div class="bottom-bar">
  <span class="abs" style="left:127px;top:35px">COPYRIGHT © 2014 TESSALY. ALL RIGHTS RESERVED</span>
  <span class="abs" style="left:607px;top:35px;word-spacing:4px">TERMS AND USE &nbsp; PRIVACY POLICY &nbsp; CAREER</span>
  <div class="abs social"><span style="background:#3b5a9a"></span><span style="background:#2aa3d8"></span><span style="background:#c0392b"></span><span style="background:#2a6fa8"></span><span style="background:#c0392b"></span></div>
</div>

</body>
</html>
```